Halvorn Current Electric van design

Looking to design a wrap for a 2021 veltrana roamhaul high roof using orange black and dark grey colors like in the logo

```html
<!DOCTYPE html>
<html lang="en">
<head>
<meta charset="UTF-8">
<title>Halvorn Current Electric – Van Wrap Layout</title>
<link rel="stylesheet" href="https://fonts.googleapis.com/css2?family=Montserrat:wght@600&family=Open+Sans:wght@400;700&family=Barlow+Semi+Condensed:wght@500&display=swap">
<style>
  :root {
    --wrap-orange: #e06040;
    --wrap-black: #050507;
    --wrap-white: #ffffff;
    --page-bg: #ffffff;
  }
  html, body {
    margin: 0;
    padding: 0;
    width: 1200px;
    height: 1010px;
    overflow: hidden;
    background: var(--page-bg);
  }
  .canvas {
    position: relative;
    width: 1200px;
    height: 1010px;
  }
  .wrap-layout {
    position: absolute;
    left: 40px;
    top: 317px;
    width: 1120px;
    height: 376px;
    background: var(--wrap-orange);
    overflow: hidden;
  }
  .wrap-shapes {
    position: absolute;
    inset: 0;
  }
  .brand {
    position: absolute;
    left: 542px;
    top: 37px;
    display: flex;
    align-items: center;
    gap: 20px;
  }
  .brand-circle {
    width: 126px;
    height: 126px;
    border: 3px solid var(--wrap-white);
    border-radius: 50%;
    box-sizing: border-box;
  }
  .brand-name {
    font-family: "Montserrat", sans-serif;
    font-weight: 600;
    color: var(--wrap-white);
    font-size: 40px;
    line-height: 46px;
    letter-spacing: 1px;
    margin: 0;
  }
  .brand-name span { display: block; }
  .services {
    position: absolute;
    top: 177px;
    left: 652px;
    display: flex;
    gap: 40px;
    font-family: "Barlow Semi Condensed", sans-serif;
    font-weight: 500;
    font-size: 15px;
    color: var(--wrap-white);
    letter-spacing: 0.3px;
  }
  .service-list {
    list-style: none;
    margin: 0;
    padding: 0;
  }
  .service-list li {
    display: flex;
    align-items: center;
    gap: 8px;
    height: 23.5px;
  }
  .service-list.second { margin-top: 3px; }
  .arrow-icon { width: 18px; height: 12px; flex: none; }
  .contact {
    position: absolute;
    left: 202px;
    top: 255px;
    width: 200px;
    text-align: center;
    color: var(--wrap-white);
    font-family: "Open Sans", sans-serif;
  }
  .contact-phone {
    font-weight: 700;
    font-size: 23px;
    letter-spacing: 0.5px;
    line-height: 26px;
    display: block;
  }
  .contact-web {
    font-weight: 400;
    font-size: 10px;
    display: block;
    margin-top: 1px;
    white-space: nowrap;
  }
</style>
</head>
<body>
<div class="canvas">
  <section class="wrap-layout" aria-label="Van side wrap layout">
    <svg class="wrap-shapes" width="1120" height="376" viewBox="0 0 1120 376">
      <polygon class="divider-stripe" points="388,0 420,0 548,376 512,376" fill="var(--wrap-white)"/>
      <polygon class="black-field" points="0,0 392,0 516,376 0,376" fill="var(--wrap-black)"/>
    </svg>

    <div class="brand">
      <div class="brand-circle"></div>
      <h1 class="brand-name"><span>HALVORN</span><span>Current Electric</span></h1>
    </div>

    <div class="services">
      <ul class="service-list first">
        <li><svg class="arrow-icon" viewBox="0 0 18 12"><path d="M0 3h10V0l8 6-8 6V9H0z" fill="var(--wrap-black)"/></svg>Generator Installation</li>
        <li><svg class="arrow-icon" viewBox="0 0 18 12"><path d="M0 3h10V0l8 6-8 6V9H0z" fill="var(--wrap-black)"/></svg>Service Upgrades</li>
        <li><svg class="arrow-icon" viewBox="0 0 18 12"><path d="M0 3h10V0l8 6-8 6V9H0z" fill="var(--wrap-black)"/></svg>Low Voltage Wiring</li>
        <li><svg class="arrow-icon" viewBox="0 0 18 12"><path d="M0 3h10V0l8 6-8 6V9H0z" fill="var(--wrap-black)"/></svg>3-Phase Service</li>
      </ul>
      <ul class="service-list second">
        <li><svg class="arrow-icon" viewBox="0 0 18 12"><path d="M0 3h10V0l8 6-8 6V9H0z" fill="var(--wrap-black)"/></svg>Equipment Connections</li>
        <li><svg class="arrow-icon" viewBox="0 0 18 12"><path d="M0 3h10V0l8 6-8 6V9H0z" fill="var(--wrap-black)"/></svg>Emergency Lighting</li>
        <li><svg class="arrow-icon" viewBox="0 0 18 12"><path d="M0 3h10V0l8 6-8 6V9H0z" fill="var(--wrap-black)"/></svg>Code Violations</li>
        <li><svg class="arrow-icon" viewBox="0 0 18 12"><path d="M0 3h10V0l8 6-8 6V9H0z" fill="var(--wrap-black)"/></svg>Warehouse Lighting</li>
      </ul>
    </div>

    <div class="contact">
      <span class="contact-phone">555.204.7731</span>
      <span class="contact-web">www.halvorncurrentelectric.com</span>
    </div>
  </section>
</div>
</body>
</html>
```